Redesign of business card for Cedar Ridge Mechanical

We are looking for a new design for our business cards for Cedar Ridge Mechanical. We are a plumbing & HVAC construction company, operating on the West Coast of Canada and USA. Logo attached.
Industry/Entity Type
Construction - Plumbing & HVAC
Contact Information for Business Card
Name, address, phone numbers, email, website address
Look and feel
Each slider illustrates characteristics of the customer's brand and the style your logo design should communicate.

```html
<!DOCTYPE html>
<html lang="en">
<head>
<meta charset="utf-8">
<title>Cedar Ridge Mechanical — Business Card</title>
<link href="https://fonts.googleapis.com/css2?family=Inter:wght@400;600;700&display=swap" rel="stylesheet">
<style>
  :root {
    --backdrop: #9a9a9a;
    --card-front: #ffffff;
    --card-back-top: #475163;
    --card-back-bottom: #535d6d;
    --ink: #111111;
    --ink-muted: #a8a8a8;
    --sketch-tint: #e6e8f2;
    --pattern-tint: rgba(40, 48, 62, 0.35);
    --on-dark: #ffffff;
  }
  * { box-sizing: border-box; margin: 0; padding: 0; }
  html, body { width: 1200px; height: 1000px; overflow: hidden; }
  body {
    background: var(--backdrop);
    font-family: "Inter", Arial, sans-serif;
    color: var(--ink);
    position: relative;
  }
  .card {
    position: absolute;
    left: 293px;
    width: 615px;
    height: 353px;
    border-radius: 18px;
    overflow: hidden;
    box-shadow: 0 10px 18px rgba(0, 0, 0, 0.22);
  }
  .card--front { top: 90px; background: var(--card-front); }
  .card--back {
    top: 500px;
    background: linear-gradient(180deg, var(--card-back-top), var(--card-back-bottom));
  }

  .building-sketch {
    position: absolute;
    left: 470px; top: 0;
    width: 438px; height: 340px;
    background:
      linear-gradient(180deg, rgba(255,255,255,0) 55%, #fff 100%),
      linear-gradient(90deg, #fff 0%, var(--sketch-tint) 45%, #f1f2f7 100%);
    left: 177px;
  }

  .brand-name {
    position: absolute;
    font-weight: 700;
    letter-spacing: 0.02em;
    text-transform: uppercase;
    display: flex;
    align-items: center;
    gap: 10px;
    line-height: 1.1;
  }
  .brand-name__square {
    width: 34px; height: 34px;
    border: 3px solid currentColor;
    border-radius: 4px;
    flex: none;
  }
  .card--front .brand-name { left: 67px; top: 47px; font-size: 15px; color: var(--ink); }
  .card--back .brand-name { right: 59px; top: 241px; font-size: 15px; color: var(--on-dark); }

  .person { position: absolute; left: 67px; top: 144px; }
  .person__name { font-size: 24px; font-weight: 700; line-height: 1.1; }
  .person__role { font-size: 17px; color: var(--ink-muted); margin-top: 1px; }

  .address {
    position: absolute; left: 67px; top: 207px;
    font-size: 14px; line-height: 17px; font-style: normal;
  }
  .contact { position: absolute; left: 67px; top: 274px; list-style: none; font-size: 14px; line-height: 17px; }
  .contact li { display: flex; align-items: center; gap: 8px; }
  .contact svg { width: 13px; height: 13px; flex: none; }

  .website { position: absolute; right: 75px; top: 291px; font-size: 14px; line-height: 17px; }
  .website strong { font-weight: 700; }

  .mark-pattern {
    position: absolute; inset: 0;
    background:
      linear-gradient(135deg, var(--pattern-tint) 0%, rgba(40,48,62,0.15) 50%, rgba(255,255,255,0.06) 100%);
  }
</style>
</head>
<body>
  <section class="card card--front">
    <div class="building-sketch" role="img" aria-label="Faint line sketch of a modern multi-storey building"></div>

    <div class="brand-name"><span class="brand-name__square"></span><span>Cedar Ridge<br>Mechanical</span></div>

    <div class="person">
      <h1 class="person__name">Name Surname</h1>
      <p class="person__role">Position</p>
    </div>

    <address class="address">4120 Harbor View Road<br>Suite 210, Tustin<br>CA 92780</address>

    <ul class="contact">
      <li>
        <svg viewBox="0 0 16 16"><path fill="#111" d="M3.6 1.2 6 3.6c.4.4.4 1 0 1.4L4.9 6.1a9 9 0 0 0 5 5L11 10c.4-.4 1-.4 1.4 0l2.4 2.4c.4.4.4 1 0 1.4l-1.3 1.3C11 16.5 6.3 14 3.6 11.4.9 8.7-1.4 4 .9 1.5L2.2.2c.4-.4 1-.4 1.4 1z"/></svg>
        <span>213-555-0148</span>
      </li>
      <li>
        <svg viewBox="0 0 16 16"><path fill="#111" d="M1 3h14v10H1z"/><path fill="none" stroke="#fff" stroke-width="1.3" d="M1.5 3.7 8 9l6.5-5.3"/></svg>
        <span>info@cedarridgemech.com</span>
      </li>
    </ul>

    <p class="website"><strong>cedarridgemech</strong>.com</p>
  </section>

  <section class="card card--back">
    <div class="mark-pattern" role="img" aria-label="Faint repeating brand mark pattern"></div>
    <div class="brand-name"><span class="brand-name__square"></span><span>Cedar Ridge<br>Mechanical</span></div>
  </section>
</body>
</html>
```